Birch Hauling Business Card Design Project

We need a new company business card. We provide professional timber harvesting (logging) and forest management services. I'm open to any creative design. Most company caps and shirts are navy blue and Light grey. Logo does not necessarily have to contain those colors. Logo containing picture of logging equipment, log truck, trees, or logs are acceptable. Be creative. Final logo should communicate our company's pride and professionalism in the East Texas Timber Industry.
Updates

Target Market(s)

Timber owners, sawmills, and forestry professionals

Industry/Entity Type

Business

Requirements
Must have
• Must have Contact Info.
Phone: 936-402-5917
address: PO Box 4830
Pine Hollow, Tx 75991
www.jmbirchhauling.example
jmbirchhauling@mailbox.example
Owner: Jared Marsh

Or design must leave room for this info.

```html
<!DOCTYPE html>
<html lang="en">
<head>
<meta charset="utf-8">
<title>Birch Hauling Business Card</title>
<link href="https://fonts.googleapis.com/css2?family=Orbitron:wght@700&family=Cinzel:wght@400;700&display=swap" rel="stylesheet">
<style>
  :root {
    --backdrop: #e6e6e6;
    --paper: #f7f7f7;
    --navy: #2e3282;
    --navy-light: #444a9c;
    --navy-deep: #1e2163;
    --band-dark: #2b2b2b;
    --band-light: #6b6b6b;
    --ink-light: #e4e6f4;
    --white: #ffffff;
  }
  * { box-sizing: border-box; margin: 0; padding: 0; }
  html, body {
    width: 1200px; height: 720px; overflow: hidden;
    background: var(--backdrop);
  }
  .canvas { position: relative; width: 1200px; height: 720px; }

  .card {
    position: absolute; top: 242px;
    width: 420px; height: 240px; overflow: hidden;
  }
  .card--front { left: 147px; background: var(--paper); }
  .card--back {
    left: 633px;
    background: radial-gradient(ellipse at 40% 35%, var(--navy-light) 0%, var(--navy) 55%, var(--navy-deep) 100%);
  }

  .logo-text {
    position: absolute; left: 0; right: 0;
    text-align: center;
    font-family: "Orbitron", sans-serif;
    font-weight: 700;
    font-size: 22px; letter-spacing: 1px;
    line-height: 1;
    white-space: nowrap;
  }
  .card--front .logo-text { top: 45px; color: var(--navy); }
  .card--back .logo-text { top: 108px; color: var(--white); }

  .name-band {
    position: absolute; left: 0; top: 115px;
    width: 100%; height: 31px;
    background: linear-gradient(90deg, var(--band-dark) 0%, var(--band-light) 50%, var(--band-dark) 100%);
    display: flex; align-items: center; justify-content: center; gap: 5px;
    color: var(--white);
    font-family: "Cinzel", serif;
  }
  .name-band__name { font-weight: 700; font-size: 13px; }
  .name-band__divider { font-size: 13px; }
  .name-band__title { font-size: 9.5px; letter-spacing: 0.3px; }

  .contact-panel {
    position: absolute; left: 0; top: 153px;
    width: 100%; height: 87px;
    background: linear-gradient(180deg, var(--navy) 0%, var(--navy-light) 45%, var(--navy) 100%);
    color: var(--ink-light);
    font-family: "Cinzel", serif;
    font-size: 9.5px;
  }
  .contact-list { position: absolute; left: 25px; top: 31px; list-style: none; }
  .contact-list li { display: flex; align-items: center; gap: 7px; height: 12px; white-space: nowrap; }
  .contact-list svg { width: 11px; height: 9px; flex: none; }
  .mailing-address {
    position: absolute; right: 24px; top: 37px;
    text-align: right; font-style: normal; line-height: 12px; white-space: nowrap;
  }
</style>
</head>
<body>
<main class="canvas">
  <section class="card card--front" aria-label="Business card front">
    <p class="logo-text">YOUR LOGO HERE</p>
    <div class="name-band">
      <span class="name-band__name">Jared Marsh</span>
      <span class="name-band__divider">|</span>
      <span class="name-band__title">President</span>
    </div>
    <div class="contact-panel">
      <ul class="contact-list">
        <li>
          <svg viewBox="0 0 11 9" aria-hidden="true"><path d="M1 3 Q5.5 0 10 3 L9 4 L7.5 3.4 L7.5 2.6 Q5.5 2 3.5 2.6 L3.5 3.4 L2 4 Z M3 4.5 H8 L9.5 8 H1.5 Z" fill="currentColor"/></svg>
          <span>Phone: 936-402-5917</span>
        </li>
        <li>
          <svg viewBox="0 0 11 9" aria-hidden="true"><rect x="0.5" y="1" width="10" height="7" fill="currentColor"/><path d="M0.5 1 L5.5 5 L10.5 1 M0.5 8 L4 4.5 M10.5 8 L7 4.5" stroke="#2e3282" stroke-width="0.9" fill="none"/></svg>
          <span>jmbirchhauling@mailbox.example</span>
        </li>
        <li>
          <svg viewBox="0 0 11 9" aria-hidden="true"><rect x="1" y="1" width="9" height="6" fill="none" stroke="currentColor" stroke-width="1.1"/><rect x="4" y="7" width="3" height="1.5" fill="currentColor"/></svg>
          <span>www.jmbirchhauling.example</span>
        </li>
      </ul>
      <address class="mailing-address">PO Box 4830<br>Pine Hollow, Tx 75991</address>
    </div>
  </section>

  <section class="card card--back" aria-label="Business card back">
    <p class="logo-text">YOUR LOGO HERE</p>
  </section>
</main>
</body>
</html>
```